Tidewell Horizon Magazine need Logo desing and front page for 1 edittion

This is a new magazine that will be circulating in Panama. the magazine will run non for profit,will be mostly informative and few advertizers to cover printing costs.
the magaine will oncce every 2 or 3 month. we need to present it to the editors who will be aproving or diss aproving the project.

we need a Logo desing for the name of the magazine "Tidewell Horizon" and the "front cover desing for the first edition" it will be good if the designer can incude the designed format for the iner magazine, for us just to add in the artucles and the spaces for advertizing.

the magazine content will be articles by govenment energy sectors, gloval warming articles, articles in renewvable enery, university profesor talking or promoting new ideas or university advances, orientations, special edition on book or international articles about the subject on saving enerty, different sectors, world innovations in renewbable energy, and the companies who will advertize will be comapnies selling VORN products, companies offfering product and services on renewvable energy, Led product and systems companies etc...

Printing

```html
<!DOCTYPE html>
<html lang="en">
<head>
<meta charset="utf-8">
<title>The green machine – Tidewell Horizon spread</title>
<link href="https://fonts.googleapis.com/css2?family=Playfair+Display:wght@700&family=Jost:ital,wght@0,300;0,400;0,500;1,400&display=swap" rel="stylesheet">
<style>
  :root{
    --green:#2ba64a;
    --green-box:#25a844;
    --blue:#0b86bd;
    --ink:#1d1d1b;
    --paper:#ffffff;
    --photo-light:#eef0ef;
    --photo-mid:#c9cecc;
    --photo-dark:#9da3a1;
    --photo-accent:#7dc242;
  }
  *{margin:0;padding:0;box-sizing:border-box}
  html,body{width:1200px;height:776px;overflow:hidden;background:var(--paper)}
  .spread{position:relative;width:1200px;height:776px;color:var(--ink);font-family:"Jost",sans-serif}
  .abs{position:absolute}

  .section-bar{left:28px;top:27px;width:544px;height:23px;background:var(--blue);color:#fff;
    font-family:"Playfair Display",serif;font-size:17px;line-height:23px;padding-left:4px;font-weight:700}

  .headline{left:26px;top:118px;font-family:"Playfair Display",serif;font-weight:700;color:var(--green);
    font-size:103px;line-height:100px;letter-spacing:0}
  .standfirst{left:440px;top:238px;font-style:italic;font-size:24px;line-height:30px;color:var(--ink)}

  .column{font-size:11.9px;line-height:15.3px;text-align:justify;hyphens:auto;overflow:hidden}
  .column p{margin:0}
  .column h2{font-family:"Playfair Display",serif;font-weight:700;color:var(--green);font-size:16.5px;
    line-height:20px;margin:12px 0 2px;text-align:left}
  .drop-cap{float:left;font-size:78px;line-height:60px;margin:2px 5px 0 -3px;font-weight:300;color:var(--ink)}

  .col-1{left:28px;top:362px;width:263px;height:378px}
  .col-2{left:309px;top:362px;width:263px;height:378px}
  .col-3{left:628px;top:408px;width:264px;height:332px}
  .col-4{left:910px;top:408px;width:262px;height:192px}

  .hero-photo{left:612px;top:0;width:588px;height:400px;
    background:linear-gradient(160deg,var(--photo-light) 0%,var(--photo-mid) 55%,var(--photo-dark) 100%)}
  .hero-photo::before{content:"";position:absolute;left:12px;top:74px;width:78px;height:312px;
    background:var(--photo-accent);opacity:.55}

  .opinion-box{left:908px;top:604px;width:264px;height:131px;background:var(--green-box);border-radius:10px;
    color:#fff;padding:7px 10px}
  .opinion-box h3{font-family:"Playfair Display",serif;font-weight:700;font-size:18.5px;line-height:24px;margin-bottom:4px}
  .opinion-box p{font-style:italic;font-size:12.3px;line-height:18px}

  .folio{top:746px;font-size:12px;line-height:16px}
  .folio-left{left:28px}
  .folio-right{left:1158px}
  .masthead-name{top:746px;font-family:"Playfair Display",serif;font-weight:700;font-size:12px;line-height:16px;color:var(--green)}
  .masthead-left{right:628px}
  .masthead-right{left:628px}
</style>
</head>
<body>
<main class="spread">
  <div class="abs section-bar">Technology</div>

  <h1 class="abs headline">The green<br>machine</h1>
  <p class="abs standfirst">What is it<br>and why do<br>we love it?</p>

  <div class="abs hero-photo" role="img" aria-label="White electric car plugged into a green charging station"></div>

  <article class="abs column col-1">
    <p><span class="drop-cap">K</span>o hi, obus sesid confex sena nonstum nonsultorio, taliciam, quium ince­pesNon tem verissu libusa re muscem iumus, et;To elicaet? Risquam tereis. Cessenam sa vernis verbis ac movirtil huideni hiBi incemus adducercem, nonverri patanum estrionsunt, que arbi fit.</p>
    <p>Tor untiu voc mius et ventus, ficte, que prox manteret iliamquit; ne forteli, nostraedees vis, utus for adela manum adhum iam nostreb efaceris, ut verfex nos viconum nonsulegili iaequam crissus ceme di pris. Robut acchuid erfirib utebatiam sens se, trarter estrice lissidi pra vestracta vastis. Valabulvili, Cat.</p>
    <h2>What can it do?</h2>
    <p>Si iaequa reviliculus cris. Ad mum cae clego avo, morte, Paliamed con andientiliam usquonf ecurorae ne confina tustre, te non hos in peris dem dum tuam nicultus, cae nosta vividelatrum con vero cae iam utus for adela manum adhum iam nostreb efaceris, ut verfex nos viconum nonsulegili utus for adela</p>
  </article>

  <article class="abs column col-2">
    <p>manum adhum iam nostreb efaceris, ut verfex nos viconum nonsulegili perce eorteris. Graet ia deffrem arei im noximussa rescrum porum consusq uamendit quod nostemus. Aximus lissi fachucta, lint iliciam poXimedii considiu consissastide liconsula duconihicam hus</p>
    <h2>The meanings</h2>
    <p>publiae convere contere ssedo, cone alestia noca aderobus in ac mo aude ad co ut finam publis. Do, quit? quontina, consus pra milii senirium inam hors inensum publibus opubliciem halicam prore caed auctur, Catis, conostordius nonfecitiam, de confirtiam. Tor untiu voc mius et ventus, ficte, que prox manteret iliamquit; ne forteli, nostraedees vis, utus for adela</p>
    <p>Rae inatebatum lostem aut factum ori se fex moltum nostimus ilibus henatus iam ego publicae iam perce eorteris. Graet ia deffrem arei fur hillari pionsup ientebus bonum, tississulius macii etodit pratimurs M. Vala pos ne mena, quo nostis; nocrum untem haberius, potique.</p>
  </article>

  <article class="abs column col-3">
    <p>Tor untiu voc mius et ventus, ficte, que prox manteret iliamquit; ne forteli, nostraedees vis, ego publicae iam perce eo utus for adela senimortiam tes vivatus vis eo, nonlocur hae cae. Batea con tissit. Fultorum senterd icaetratusa ex mei tus, pra tat conemus publius audactu es At gratis, quonicae capere coristrum mur, sisquo erfec ta dientesul vignon sicae con Italario, cons a occii tuidit. Simil tabus conte, fica; nentem tem sus confes apes voltursum vidit ves publisq uidiurs peritanum, et ignatuscidem Romnim pricati, caed nonfecipio, quodie coerit, quo mus, quius, num efesimus nos ficenat urnitat</p>
    <h2>So, really - what can it do?</h2>
    <p>ifectuius furente caed poti imus il vit virma, popublicae consisula in vicae duc ina, ne cons intis habus condam hebatu vastruntrae acia spio, nonsultum nons cretorum que apere</p>
  </article>

  <article class="abs column col-4">
    <p>egerra voltis.</p>
    <p>Ibem omperitis. Abem publium dere cerum uterio, num hocaelu deorunt eresimis. Mis atus, ca; ia audernum sertum nocavest intiam intra, uteroximuri publiustum hilicae nocchui tampractorei pati publius, consum dicio vide contrav ehebulica pubis hos condium austea mus, con tere adepos sederunique addum in tus, opublici iam ac menatium detri patiam int. Opublique cesse inatussum simo eticae firmaximo ute, P. Habuntr ituam, peciem inclu</p>
  </article>

  <aside class="abs opinion-box">
    <h3>Your opinion matters to us</h3>
    <p>ZDe es, fordiem overic tus, que aperess erimus iam nonsula vit, con aceste nes, quo C. Go me cum incepon iuspio et, inatum inatilles vius nortum ad des habem se desimpostem untrudemus se confecto</p>
  </aside>

  <footer>
    <span class="abs folio folio-left">10</span>
    <span class="abs masthead-name masthead-left">Tidewell Horizon</span>
    <span class="abs masthead-name masthead-right">Tidewell Horizon</span>
    <span class="abs folio folio-right">11</span>
  </footer>
</main>
</body>
</html>
```